BOLD & MINIMALIST DESIGN NEEDED

We want a very bold but minimalistic business card design that is impactful and utilizes both sides of the business card. Our current logo is included for your use.

We want bold fonts and good use of negative space. We don't want the logo to overpower the design.

Target Market(s)

Professionals who are building new commercial buildings.

Industry/Entity Type

Construction

Contact Information for Business Card

Name, Title, email, office phone, cell phone, website

Font styles to use
Serif
Sans Serif

Requirements
Must have
• Bold design!

```html
<!DOCTYPE html>
<html lang="en">
<head>
<meta charset="utf-8">
<title>Northridge Design + Build — Business Card</title>
<link rel="stylesheet" href="https://fonts.googleapis.com/css2?family=Archivo:wght@400;800&display=swap">
<style>
  :root {
    --backdrop: #7a7a7a;
    --card-white: #f4f4f5;
    --ink: #111111;
    --green-light: #b3d67c;
    --green: #8cc63f;
    --green-deep: #74b21e;
    --white: #ffffff;
  }
  * { margin: 0; padding: 0; box-sizing: border-box; }
  html, body {
    width: 1200px; height: 900px; overflow: hidden;
    background: var(--backdrop);
    font-family: "Archivo", Arial, sans-serif;
    color: var(--ink);
  }
  .canvas {
    position: relative; width: 1200px; height: 900px;
  }
  .card {
    position: absolute; left: 268px;
    width: 664px; height: 380px;
    border-radius: 26px;
    overflow: hidden;
  }
  .card-front { top: 50px; background: var(--card-white); }
  .card-back {
    top: 470px;
    background: radial-gradient(ellipse at 55% 45%, var(--green-light) 0%, var(--green) 55%, var(--green-deep) 100%);
  }

  .front-wordmark {
    position: absolute; inset: 0;
    display: flex; flex-direction: column; align-items: center; justify-content: center;
    gap: 10px;
  }
  .wordmark-name {
    font-weight: 800; font-size: 46px; letter-spacing: 1px; text-transform: uppercase;
    display: flex; align-items: center; gap: 14px;
  }
  .wordmark-dot { width: 20px; height: 20px; background: var(--green); border-radius: 50%; }
  .wordmark-sub {
    font-weight: 400; font-size: 16px; letter-spacing: 9px; text-transform: uppercase;
    border-top: 1.5px solid var(--ink); padding-top: 6px;
  }

  .back-brand {
    position: absolute; right: 64px; top: 52px;
    font-weight: 800; font-size: 24px; text-transform: uppercase; letter-spacing: 1px;
  }
  .back-address {
    position: absolute; right: 64px; top: 118px;
    text-align: right; font-size: 15px; line-height: 1.35;
  }
  .back-rule {
    position: absolute; left: 56px; right: 64px; top: 186px;
    border-top: 1.5px solid var(--ink);
  }
  .person {
    position: absolute; left: 56px; top: 206px;
  }
  .person-name { font-weight: 800; font-size: 28px; text-transform: uppercase; line-height: 1.05; }
  .person-title { font-size: 17px; color: var(--white); margin-top: 2px; }
  .contact-list {
    position: absolute; left: 56px; top: 276px;
    list-style: none; font-size: 17px; line-height: 1.3;
    border-top: 1.5px solid var(--ink); padding-top: 8px; width: 260px;
  }
  .contact-item { display: flex; align-items: center; gap: 10px; white-space: nowrap; }
  .contact-icon { width: 14px; height: 14px; flex: none; }
</style>
</head>
<body>
<main class="canvas">
  <section class="card card-front" aria-label="Card front">
    <div class="front-wordmark">
      <div class="wordmark-name"><span class="wordmark-dot"></span>Northridge</div>
      <div class="wordmark-sub">Design + Build</div>
    </div>
  </section>

  <section class="card card-back" aria-label="Card back">
    <div class="back-brand">Northridge</div>
    <address class="back-address" style="font-style:normal">
      2170 Alder Crest Road<br>Maple Hollow, NY 10990
    </address>
    <div class="back-rule"></div>
    <div class="person">
      <div class="person-name">Marcus Hale</div>
      <div class="person-title">President</div>
    </div>
    <ul class="contact-list">
      <li class="contact-item">
        <svg class="contact-icon" viewBox="0 0 16 16" aria-hidden="true"><path fill="#111" d="M3.5 1l2.5 3-1.5 1.8c.9 2 2.7 3.8 4.7 4.7L11 9l3 2.5-1.5 2.8C7 14 2 9 1.7 3z"/></svg>
        (555) 0142-7781
      </li>
      <li class="contact-item">
        <svg class="contact-icon" viewBox="0 0 16 16" aria-hidden="true"><rect x="1" y="3" width="14" height="10" fill="#111"/><path d="M1 3l7 6 7-6" fill="none" stroke="#8cc63f" stroke-width="1.4"/></svg>
        info@northridgebuild.com
      </li>
      <li class="contact-item">
        <svg class="contact-icon" viewBox="0 0 16 16" aria-hidden="true"><circle cx="8" cy="8" r="7" fill="#111"/><path d="M1 8h14M8 1c3 3 3 11 0 14M8 1c-3 3-3 11 0 14" fill="none" stroke="#8cc63f" stroke-width="1"/></svg>
        www.northridgebuild.com
      </li>
    </ul>
  </section>
</main>
</body>
</html>
```